Varnex Consulting Business card design.

See our website www.varnexconsulting.example which will give you a good idea of what we are about. The font is called 'Play'.

I'd like a standout business card in keeping with the themes and branding on the website

Target Market(s)

professionals. HR directors

Industry/Entity Type

Business

Contact Information for Business Card

Varnex Consulting PO Box 3172 Merrowdale NSW 2291 1300 485 193 Gavin Threlkeld Principal email: career@varnexconsulting.example ABN: 71203948865

Font styles to use
Other font styles liked:
• Play

Requirements
Must have
• Must have same design colours and branding as website.
• On back I'd prefer a list of the things we do which appears below the name at the header on the website

```html
<!DOCTYPE html>
<html lang="en">
<head>
<meta charset="utf-8">
<title>Varnex Consulting – Business Card</title>
<link rel="stylesheet" href="https://fonts.googleapis.com/css2?family=Play:wght@400;700&display=swap">
<style>
  :root {
    --backdrop: #2e2926;
    --navy: #0d2339;
    --blue: #1b8bd6;
    --white: #ffffff;
    --ink: #2b2f36;
    --rule: #8a9099;
    --track: #7a4038;
    --skin: #c99a88;
  }
  * { box-sizing: border-box; margin: 0; padding: 0; }
  html, body { width: 1200px; height: 799px; overflow: hidden; }
  body {
    background: var(--backdrop);
    font-family: "Play", sans-serif;
    position: relative;
  }
  .card {
    position: absolute;
    top: 242px;
    width: 520px;
    height: 316px;
    overflow: hidden;
    background: var(--white);
    box-shadow: 0 10px 24px rgba(0,0,0,.35);
  }
  .card--front { left: 50px; }
  .card--back { left: 630px; }

  .brand-band {
    background: var(--navy);
    padding: 22px 28px 0;
  }
  .card--front .brand-band { height: 112px; }
  .card--back .brand-band { height: 104px; text-align: right; padding-right: 26px; }

  .brand-name {
    color: var(--white);
    font-size: 34px;
    font-weight: 400;
    letter-spacing: 1px;
    line-height: 1;
  }
  .services {
    margin-top: 10px;
    color: var(--blue);
    font-size: 11px;
    letter-spacing: .6px;
    white-space: nowrap;
  }

  .details {
    position: relative;
    height: 204px;
    padding: 22px 26px;
  }
  .person-name { color: var(--blue); font-size: 16px; }
  .person-role { color: var(--ink); font-size: 14px; margin-top: 2px; }
  .divider {
    position: absolute;
    left: 238px;
    top: 72px;
    width: 1px;
    height: 112px;
    background: var(--rule);
  }
  .contact-list {
    position: absolute;
    left: 256px;
    top: 78px;
    list-style: none;
    color: var(--ink);
    font-size: 12.5px;
  }
  .contact-list li {
    display: flex;
    align-items: center;
    gap: 9px;
    height: 22px;
  }
  .contact-list .abn { margin-bottom: 6px; }
  .contact-icon { width: 12px; height: 12px; flex: none; }

  .hero-photo {
    height: 212px;
    background:
      linear-gradient(160deg, rgba(13,35,57,.9) 0%, rgba(13,35,57,0) 35%),
      linear-gradient(100deg, var(--track) 0%, var(--skin) 45%, #b98473 65%, var(--track) 100%);
  }
</style>
</head>
<body>

  <section class="card card--front" aria-label="Business card front">
    <header class="brand-band">
      <h1 class="brand-name">VARNEX CONSULTING</h1>
      <p class="services">Search &amp; Select | Career | Coaching | Leadership | Outplacement</p>
    </header>
    <div class="details">
      <p class="person-name">Gavin Threlkeld</p>
      <p class="person-role">Principal</p>
      <span class="divider"></span>
      <ul class="contact-list">
        <li class="abn">ABN: 71203948865</li>
        <li>
          <svg class="contact-icon" viewBox="0 0 12 12" aria-hidden="true">
            <rect width="12" height="12" rx="1.5" fill="var(--navy)"/>
            <path d="M3.6 2.8l1.3 1.4-.7 1.1c.5 1 1.3 1.8 2.3 2.3l1.1-.7 1.4 1.3-.8 1.1C5.6 9 3 6.4 2.8 3.6z" fill="var(--white)"/>
          </svg>
          1300 485 193
        </li>
        <li>
          <svg class="contact-icon" viewBox="0 0 12 12" aria-hidden="true">
            <rect width="12" height="12" rx="1.5" fill="var(--navy)"/>
            <rect x="2.5" y="3.5" width="7" height="5" fill="none" stroke="var(--white)" stroke-width="1"/>
            <path d="M2.5 3.5L6 6.3 9.5 3.5" fill="none" stroke="var(--white)" stroke-width="1"/>
          </svg>
          career@varnexconsulting.example
        </li>
        <li>
          <svg class="contact-icon" viewBox="0 0 12 12" aria-hidden="true">
            <rect width="12" height="12" rx="1.5" fill="var(--navy)"/>
            <path d="M6 10S3.2 6.8 3.2 5a2.8 2.8 0 015.6 0C8.8 6.8 6 10 6 10z" fill="var(--white)"/>
            <circle cx="6" cy="5" r="1" fill="var(--navy)"/>
          </svg>
          PO Box 3172 Merrowdale NSW 2291
        </li>
      </ul>
    </div>
  </section>

  <section class="card card--back" aria-label="Business card back">
    <header class="brand-band">
      <h2 class="brand-name">VARNEX CONSULTING</h2>
      <p class="services">Search &amp; Select | Career | Coaching | Leadership | Outplacement</p>
    </header>
    <div class="hero-photo" role="img" aria-label="Photograph of sprinters' hands on the starting line of a running track"></div>
  </section>

</body>
</html>
```